Private Dining Restaurant Menu Design

Looking for help in designing a private dining room menu brochure - probably would need 4 panel layout to make all of the content fit, or a 5.5x8" booklet. Open to your ideas on layout/vessel - would want to post on website and be able to print to hand out to guests interested in booking our private dining room.

All content is in the attached "Private Dining Menu".

Would like to match existing dinner menu design - also attached.

Website is www.copperkettlebistro.com

Requirements
Must have
• Easy to read format of a brochure of the private dining menu content - want to be able to hand out to interested guests and have it simple and easy to read/flip through.

```html
<!DOCTYPE html>
<html lang="en">
<head>
<meta charset="utf-8">
<title>Private Dining Room Menu – Copper Kettle Bistro</title>
<link href="https://fonts.googleapis.com/css2?family=Fjalla+One&family=Fira+Sans:wght@400;500&display=swap" rel="stylesheet">
<style>
  :root {
    --paper: #ebe8e3;
    --paper-grain: #dedad3;
    --brick: #8e2b2b;
    --ink: #26315a;
    --bear: #2b3a6b;
  }
  html, body { margin: 0; padding: 0; overflow: hidden; }
  body { width: 825px; height: 1200px; background: var(--paper); }
  .menu {
    position: relative;
    width: 825px; height: 1200px; overflow: hidden;
    background:
      repeating-linear-gradient(90deg, transparent 0 37px, rgba(0,0,0,0.025) 37px 39px, transparent 39px 83px),
      linear-gradient(180deg, var(--paper) 0%, #eeebe6 50%, var(--paper-grain) 100%);
    font-family: "Fira Sans", Arial, sans-serif;
    color: var(--ink);
  }
  .menu-title {
    position: absolute; left: 44px; top: 36px; margin: 0;
    font-family: "Fjalla One", "Arial Narrow", sans-serif;
    font-weight: 400; font-size: 37px; letter-spacing: 1px;
    color: var(--brick);
  }
  .title-rule {
    position: absolute; left: 44px; right: 36px; top: 92px;
    border-top: 2px solid var(--brick);
  }
  .section { position: absolute; left: 44px; right: 36px; }
  .section-head {
    display: flex; align-items: center; gap: 14px; margin: 0;
    font-family: "Fjalla One", "Arial Narrow", sans-serif;
    font-weight: 400; font-size: 22px; letter-spacing: 0.5px;
    color: var(--brick);
  }
  .section-head::after { content: ""; flex: 1; border-top: 2px solid var(--brick); }
  .section-note {
    margin: 2px 0 0;
    font-family: "Fjalla One", "Arial Narrow", sans-serif;
    font-size: 22px; color: var(--brick);
  }
  .items { list-style: none; margin: 0; padding: 0; width: 716px; }
  .item {
    display: flex; align-items: baseline;
    height: 24px; font-size: 14px; line-height: 24px;
  }
  .item-leader { flex: 1; margin: 0 3px; border-bottom: 1.5px dotted var(--ink); transform: translateY(-4px); }
  .appetizers { top: 112px; }
  .appetizers .items { margin-top: 42px; }
  .platters { top: 352px; }
  .platters .items { margin-top: 34px; }
  .desserts { top: 588px; }
  .desserts .items { margin-top: 40px; }
  .beverages { top: 746px; }
  .beverage-intro { margin: 30px 0 0; font-size: 14px; line-height: 24px; width: 720px; }
  .host-options { list-style: none; margin: 18px 0 0; padding: 0; font-size: 14px; line-height: 24px; }
  .bear-mark {
    position: absolute; left: 328px; top: 1030px; width: 126px; height: 120px;
  }
</style>
</head>
<body>
<main class="menu">
  <h1 class="menu-title">PRIVATE DINING ROOM MENU</h1>
  <div class="title-rule"></div>

  <section class="section appetizers">
    <h2 class="section-head">APPETIZERS (price is by the dozen)</h2>
    <ul class="items">
      <li class="item"><span>Texas Egg Rolls</span><span class="item-leader"></span><span>$25</span></li>
      <li class="item"><span>Chicken Wings (Buffalo, BBQ, OR Blackened)</span><span class="item-leader"></span><span>$12</span></li>
      <li class="item"><span>Baby Back Ribs</span><span class="item-leader"></span><span>$30</span></li>
      <li class="item"><span>Sliders (Pulled Pork or Rotisserie Chicken)</span><span class="item-leader"></span><span>$35</span></li>
      <li class="item"><span>Wood-Roasted Quesadillas</span><span class="item-leader"></span><span>$30</span></li>
      <li class="item"><span>Copper Skins</span><span class="item-leader"></span><span>$25</span></li>
    </ul>
  </section>

  <section class="section platters">
    <h2 class="section-head">PLATTERS – SMALL &amp; LARGE</h2>
    <p class="section-note">(small serves ~10-15 – large serves ~25-30)</p>
    <ul class="items">
      <li class="item"><span>Chips, Salsa, and Guacamole</span><span class="item-leader"></span><span>sm$25/lg$45</span></li>
      <li class="item"><span>Fresh Fruit Platter</span><span class="item-leader"></span><span>sm$50/lg$75</span></li>
      <li class="item"><span>Hot Artichoke Dip (comes with bread and tortilla chips)</span><span class="item-leader"></span><span>sm$30/lg$60</span></li>
      <li class="item"><span>Domestic Cheese and Crackers</span><span class="item-leader"></span><span>sm$45/lg$65</span></li>
      <li class="item"><span>Fresh Veggie Platter</span><span class="item-leader"></span><span>sm$40/lg$65</span></li>
    </ul>
  </section>

  <section class="section desserts">
    <h2 class="section-head">DESSERT OPTIONS (Price is per item)</h2>
    <ul class="items">
      <li class="item"><span>House Made Cheesecake Slice (turtle, strawberry, or plain)</span><span class="item-leader"></span><span>$5/slice</span></li>
      <li class="item"><span>Whole House Made Cheesecake (turtle, strawberry, or plain)</span><span class="item-leader"></span><span>$60 (15 slices at $4/slice)</span></li>
      <li class="item"><span>Assorted Bars and Cookie Platter (25 bars/cookies)</span><span class="item-leader"></span><span>$25</span></li>
    </ul>
  </section>

  <section class="section beverages">
    <h2 class="section-head">BEVERAGE OPTIONS</h2>
    <p class="beverage-intro">We offer a full bar with a variety of NA, liquor, beer, and wine options All beverages will be charged per menu price</p>
    <ul class="host-options">
      <li>NA Beverage Host: Soda, Iced Tea, Lemonade, Coffee, and Hot Tea hosted by renter for their guests</li>
      <li>Full Host: All NA and Alcoholic beverages to be hosted by the renter for their guests</li>
      <li>Partial Host: A set amount or certain types of beverages hosted by the renter for their guests</li>
      <li>Cash Bar: Each beverage will be paid for by each individual guest</li>
    </ul>
  </section>

  <svg class="bear-mark" viewBox="0 0 126 120" role="img" aria-label="Illustration of a walking bear in navy ink">
    <defs>
      <radialGradient id="bearTone" cx="50%" cy="55%" r="55%">
        <stop offset="0%" stop-color="#2b3a6b" stop-opacity="0.55"/>
        <stop offset="100%" stop-color="#2b3a6b" stop-opacity="0"/>
      </radialGradient>
    </defs>
    <rect width="126" height="120" fill="url(#bearTone)"/>
  </svg>
</main>
</body>
</html>
```